LEARN Business Skills so you can Earn a good living

size of the poster is 8”x 10.75" plus 0.25" bleed.
Please leave 1 inch on the bottoum for footer
I want a design a poster that will attract people's attention.
I appreciate a creative ad however the ad should not take away from being able to clearly read the text.
-I also appreciate a simple creative ad that is not too busy.
-you can use graphics, vectors, or pictures of real people.
-however, if you use real people it should be a white male that is wearing a white shirt and look like a professional person.

Target Market(s)

Potential young business people

Industry/Entity Type

education

Requirements
Must have
• easy to read the text
Nice to have
• I would like a "creative" simple ad that is easy to be read
Should not have
• pictures of women

```html
<!DOCTYPE html>
<html lang="en">
<head>
<meta charset="UTF-8">
<title>Business Enrichment Course Poster</title>
<link href="https://fonts.googleapis.com/css2?family=Cinzel:wght@700&family=DM+Sans:ital,wght@0,400;0,500;0,700;1,400&display=swap" rel="stylesheet">
<style>
  :root {
    --stage: #8b8b8b;
    --paper: #efeff0;
    --navy: #27396e;
    --blue: #2f5aa5;
    --orange: #e88a2c;
    --ink: #1f2d5a;
    --rule: #c9cad0;
    --skyline: #dcdde0;
  }
  * { margin: 0; padding: 0; box-sizing: border-box; }
  html, body { width: 1200px; height: 1200px; overflow: hidden; }
  body { background: var(--stage); font-family: "DM Sans", sans-serif; position: relative; }

  .poster {
    position: absolute; left: 188px; top: 20px;
    width: 824px; height: 1160px;
    background: var(--paper);
    overflow: hidden;
  }
  .skyline-photo {
    position: absolute; left: 0; top: 0; width: 824px; height: 720px;
    background: linear-gradient(180deg, rgba(239,239,240,0) 0%, var(--skyline) 45%, #e4e5e7 75%, rgba(239,239,240,0) 100%);
  }
  .brand-banner { position: absolute; left: 45px; top: 0; width: 223px; height: 270px; }
  .brand-name {
    position: absolute; left: 45px; top: 84px; width: 223px;
    text-align: center; color: #fff;
    font-family: "DM Sans", sans-serif; font-weight: 700;
    font-size: 36px; line-height: 46px; letter-spacing: 1px;
  }
  .hero-illustration {
    position: absolute; left: 48px; top: 358px; width: 220px; height: 209px;
    background: linear-gradient(135deg, #e6e7ec 0%, #c7d2e8 55%, #3c63ad 100%);
    border-radius: 6px;
  }
  .course-title {
    position: absolute; left: 276px; top: 392px;
    font-family: "Cinzel", serif; font-weight: 700;
    font-size: 60px; line-height: 61px; color: var(--navy);
    white-space: nowrap;
  }
  .course-title .accent { color: var(--orange); }
  .tagline {
    position: absolute; left: 0; top: 606px; width: 824px; text-align: center;
    font-style: italic; font-size: 24px; color: var(--ink);
  }
  .benefit {
    position: absolute; top: 678px; width: 220px; text-align: center;
  }
  .benefit-icon {
    width: 114px; height: 114px; margin: 0 auto;
    border-radius: 24px 24px 0 24px;
    background: linear-gradient(135deg, var(--navy), var(--blue));
    display: flex; align-items: center; justify-content: center;
  }
  .benefit-label {
    margin-top: 12px; font-weight: 500; font-size: 23px; line-height: 28px; color: var(--ink);
  }
  .divider { position: absolute; top: 673px; width: 1px; height: 186px; background: var(--rule); }
  .topics {
    position: absolute; left: 0; top: 896px; width: 824px; text-align: center;
    font-size: 17px; line-height: 29px; color: var(--ink);
  }
  .topics .sep { color: var(--orange); padding: 0 3px; }
</style>
</head>
<body>
  <div class="poster">
    <div class="skyline-photo" role="img" aria-label="Soft grey photograph of a city skyline with a tall skyscraper"></div>

    <svg class="brand-banner" viewBox="0 0 223 270" aria-hidden="true">
      <polygon points="0,0 223,0 223,265 0,240" fill="#2d5198"/>
      <polygon points="0,240 110,246 0,268" fill="#e88a2c"/>
    </svg>
    <div class="brand-name">NORVALE<br>SKILLS</div>

    <div class="hero-illustration" role="img" aria-label="Illustration of a businessman with a laptop riding a rising blue arrow"></div>

    <h1 class="course-title">BUSINESS<br>ENCRICHMENT<br><span class="accent">COURSE</span></h1>

    <p class="tagline">A proven success of helping people in their livelihoods</p>

    <div class="benefit" style="left:50px">
      <div class="benefit-icon">
        <svg width="80" height="80" viewBox="0 0 80 80" fill="none" stroke="#fff" stroke-width="3" stroke-linecap="round">
          <circle cx="38" cy="42" r="30"/>
          <circle cx="30" cy="38" r="8"/>
          <path d="M16 62c2-9 8-14 14-14s10 3 12 8"/>
          <path d="M50 56v-8M56 56v-12M62 54v-6"/>
          <polygon points="56,10 59,18 67,18 61,23 63,31 56,26 49,31 51,23 45,18 53,18" fill="#e88a2c" stroke="none"/>
        </svg>
      </div>
      <p class="benefit-label">Get a<br>Quality Job</p>
    </div>
    <div class="divider" style="left:274px"></div>
    <div class="benefit" style="left:290px">
      <div class="benefit-icon">
        <svg width="80" height="80" viewBox="0 0 80 80" fill="none" stroke="#fff" stroke-width="3" stroke-linecap="round">
          <circle cx="20" cy="20" r="11" fill="#e88a2c" stroke="none"/>
          <path d="M14 24l5-5 4 3 6-7M25 15h4v4" stroke="#27396e"/>
          <path d="M12 50h56l-5 14H17z"/>
          <path d="M52 50V14M52 22c-6 0-9-4-9-8 5 0 9 3 9 8zM52 22c6 0 9-4 9-8-5 0-9 3-9 8zM52 34c-6 0-9-4-9-8 5 0 9 3 9 8zM52 34c6 0 9-4 9-8-5 0-9 3-9 8z"/>
          <path d="M26 50c0-6 4-9 8-9M26 50c0-5-3-8-7-8"/>
        </svg>
      </div>
      <p class="benefit-label">Start/Grow<br>Your Business</p>
    </div>
    <div class="divider" style="left:527px"></div>
    <div class="benefit" style="left:542px">
      <div class="benefit-icon">
        <svg width="80" height="80" viewBox="0 0 80 80" fill="none" stroke="#fff" stroke-width="3" stroke-linecap="round" stroke-linejoin="round">
          <path d="M8 68l24-26 12 12 26-28"/>
          <path d="M58 26h12v12"/>
          <path d="M24 68l8-9 12 9H68V44"/>
          <path d="M14 12l2 5 5 2-5 2-2 5-2-5-5-2 5-2z" fill="#e88a2c" stroke="none"/>
          <path d="M28 8l1.5 4 4 1.5-4 1.5-1.5 4-1.5-4-4-1.5 4-1.5z" fill="#e88a2c" stroke="none"/>
          <path d="M22 28l1.5 4 4 1.5-4 1.5-1.5 4-1.5-4-4-1.5 4-1.5z" fill="#e88a2c" stroke="none"/>
        </svg>
      </div>
      <p class="benefit-label">Increase Your<br>Salary</p>
    </div>

    <div class="topics">
      Business Administration<span class="sep">|</span>Small Business Management<span class="sep">|</span>Finance<span class="sep">|</span>Investments<span class="sep">|</span><br>
      Computers<span class="sep">|</span>Accounting<span class="sep">|</span>Sales Marketing<span class="sep">|</span>Project Management Interviewing Skills<span class="sep">|</span><br>
      Business Law<span class="sep">|</span>Negotiation<span class="sep">|</span>Public Speaking<span class="sep">|</span>Import/Export<span class="sep">|</span>Information Technoloy<span class="sep">|</span><br>
      Distribution<span class="sep">|</span>Marketing<span class="sep">|</span>Ledgerly<span class="sep">|</span>Real Estate<span class="sep">|</span>Health Care<span class="sep">|</span>Management<span class="sep">|</span>Online Retail
    </div>
  </div>
</body>
</html>
```